Velora Medspa Home Page Design

I need a home page designed for a medical spa of which there are thousands in the US. Their primary purpose is to enhance personal beauty using non-surgical means, such as laser treatment and micro-needling. Since insurance typically doesn't cover such procedures, we are appealing to a mostly upscale end user, probably about 70% female.

Target Market(s)

Women 35-54

Industry/Entity Type

Medical cosmetics

Number of Pages Required

1 page

Font styles to use
Other font styles liked:
• I want very readable content, even by seniors. No grey copy, please. Black only.

Requirements
Must have
• This needs to be a photo-heavy design. Here's one example among hundreds to illustrate what other practices put forth to attract patients. https://www.plomavista.example/ Stock photos are fine, though I would prefer they obtained from PixFarrow since I have an account with them. Finally, for now, I'm looking for a static website, we'll do the coding ourselves. Thank you. r psare
Nice to have
• I would also like you tpo consider staggering the five areas with content and a photo on the home page where the dominant photos are not always on the left or right. I think that help provide somefluidity to the sit's overall appearance. And "smooth" is a key quality as, in mamy cases, that's what attracts patients, i.e., the promise of smoother looking skin. his style: four e
Should not have
• Nice, open layout, but not loose. The home page document I attached contains all home page content and everything you need for the navigation bar.

```html
<!DOCTYPE html>
<html lang="en">
<head>
<meta charset="utf-8">
<title>Velora Medspa — Home</title>
<link href="https://fonts.googleapis.com/css2?family=Oswald:wght@500;600&family=Rubik:wght@500&family=Poppins:wght@400;500&display=swap" rel="stylesheet">
<style>
:root{
  --plum:#9b4f76;
  --olive:#8a8a2e;
  --blush:#f6eff2;
  --blush-deep:#ece1e6;
  --ink:#111;
  --line:#c9c0c4;
  --white:#fff;
}
*{box-sizing:border-box;margin:0;padding:0}
html,body{width:1200px;height:3750px;overflow:hidden}
body{position:relative;background:var(--white);font-family:"Poppins",sans-serif;color:var(--ink)}
.abs{position:absolute}
.btn{position:absolute;display:inline-flex;align-items:center;justify-content:center;background:var(--plum);color:var(--white);border-radius:24px;font:500 15px "Rubik",sans-serif;letter-spacing:.3px;text-transform:uppercase;text-decoration:none}
.h2{font:500 38px/1.3 "Rubik",sans-serif;color:var(--ink)}
.h2 .accent{color:var(--olive)}
.copy{font-size:13.5px;line-height:25px;color:var(--ink)}
.copy.small{font-size:12.5px;line-height:24px}

/* header */
.site-header{position:absolute;top:0;left:0;width:1200px;height:90px;border-top:3px solid var(--plum);background:var(--white)}
.brand{position:absolute;display:flex;align-items:center;gap:10px;font:500 30px "Rubik",sans-serif;color:var(--plum)}
.brand .dot{width:18px;height:18px;border-radius:50%;background:var(--olive)}
.nav{position:absolute;left:388px;top:34px;display:flex;gap:28px;font-size:13px;letter-spacing:.5px}
.nav a{color:var(--ink);text-decoration:none}
.header-phone{position:absolute;left:665px;top:22px;display:flex;gap:12px;align-items:center}
.header-phone small{display:block;font-size:12px}
.header-phone strong{font-weight:400;font-size:19px;letter-spacing:1px}

/* hero */
.hero{position:absolute;top:90px;left:0;width:1200px;height:622px;background:var(--blush);overflow:hidden}
.hero-photo{position:absolute;left:-60px;top:-20px;width:695px;height:642px;border-radius:0 50% 0 0/0 50% 0 0;background:radial-gradient(circle at 50% 40%,#e8c4ad 0%,#c9a18a 35%,#b9b4b1 60%,#d9d6d6 100%)}
.hero-title{position:absolute;left:678px;top:186px;font:600 68px/1.08 "Oswald",sans-serif;text-transform:uppercase}
.hero-title .accent{color:var(--olive)}
.hero-sub{position:absolute;left:690px;top:340px;font-size:19px}

/* intro */
.intro{position:absolute;top:712px;left:0;width:1200px;height:453px}
.divider{position:absolute;left:600px;top:50px;width:1px;height:368px;background:var(--blush-deep)}

/* treatments */
.treatments{position:absolute;top:1165px;left:0;width:1200px;height:700px;background:linear-gradient(90deg,#fff 0%,#f6f3f3 40%,#eeeae8 100%);overflow:hidden}
.treat-photo{position:absolute;left:470px;top:0;width:730px;height:700px;background:radial-gradient(ellipse at 60% 40%,#e7bea6 0%,#d6ac95 30%,rgba(238,234,232,0) 70%)}
.vertical-label{position:absolute;left:60px;top:580px;transform:rotate(-90deg);transform-origin:left top;font:400 72px "Poppins",sans-serif;color:#ece9e9;letter-spacing:2px}
.h3{font:500 34px "Rubik",sans-serif}

/* other */
.other{position:absolute;top:1865px;left:0;width:1200px;height:570px;overflow:hidden}
.other-photo{position:absolute;left:95px;top:90px;width:490px;height:490px;border-radius:50%;background:radial-gradient(circle at 50% 35%,#c8c8c8 0%,#9e9e9e 45%,#ece4e8 75%)}

/* form */
.schedule{position:absolute;top:2435px;left:0;width:1200px;height:663px}
.field{position:absolute;left:620px;width:492px;height:41px;border:1px solid #333;padding:0 15px;font-size:12.5px;display:flex;align-items:center;justify-content:space-between}
.field.active{border-color:var(--plum);color:var(--plum)}
.field .caret{width:0;height:0;border-left:6px solid transparent;border-right:6px solid transparent;border-top:7px solid var(--ink)}

.map{position:absolute;top:3098px;left:0;width:1200px;height:372px;background:linear-gradient(135deg,#f2f2f2,#e6e6e6)}

/* footer */
.site-footer{position:absolute;top:3470px;left:0;width:1200px;height:280px}
.footer-title{font:500 19px "Rubik",sans-serif}
.footer-title .accent{color:var(--olive)}
.footer-list{list-style:none;font-size:13.5px;line-height:26px}
</style>
</head>
<body>

<header class="site-header">
  <div class="brand" style="left:60px;top:22px"><span>Velora Medspa</span><span class="dot"></span></div>
  <nav class="nav"><a href="#">ABOUT</a><a href="#">TREATMENTS ↓</a><a href="#">CONTACT</a></nav>
  <div class="header-phone">
    <svg width="34" height="34" viewBox="0 0 24 24" fill="none" stroke="var(--olive)" stroke-width="1.3"><path d="M5 3h4l2 5-2.5 1.5a11 11 0 005 5L15 12l5 2v4a2 2 0 01-2 2A16 16 0 013 5a2 2 0 012-2z"/></svg>
    <div><small>Serving Central Connecticut &amp; Beyond</small><strong>860-XXX-XXXX</strong></div>
  </div>
  <a class="btn" href="#" style="left:956px;top:24px;width:184px;height:38px">Free Consultation</a>
</header>

<section class="hero">
  <div class="hero-photo" role="img" aria-label="Smiling woman touching her face, city skyline in grey behind her"></div>
  <h1 class="hero-title"><span class="accent">Velora.</span><br>You’ve arrived.</h1>
  <p class="hero-sub">We Are Expert In Non-surgical Treatments</p>
  <a class="btn" href="#" style="left:682px;top:382px;width:195px;height:44px">Free Consultation</a>
</section>

<section class="intro">
  <svg class="abs" style="left:0;top:0" width="600" height="280"><polygon points="0,275 0,60 500,0" fill="var(--blush)"/></svg>
  <h2 class="h2 abs" style="right:643px;top:66px;text-align:right">The <span class="accent">Non-Surgical</span><br>Approach To A More<br>Confident You</h2>
  <div class="divider"></div>
  <p class="copy abs" style="left:641px;top:74px;width:355px">Established by Dr. Anil Mehra, M.D., F.A.C.S., Velora MedSpa employs the latest in nonsurgical cosmetic innovations to enhance your appearance and the way you feel about yourself. All Velora procedures are non-surgical as we effect healthier, younger-looking skin, facial reshaping, scar and hair removal numerous other results. Have concerns? Contact us now so we can help put your mind at ease. That’s the essence of Velora.</p>
  <a class="btn" href="#" style="left:640px;top:322px;width:213px;height:42px">Learn More About Us</a>
</section>

<section class="treatments">
  <div class="treat-photo" role="img" aria-label="Woman with hair up, hand resting on her shoulder"></div>
  <div class="vertical-label">TREATMENTS</div>
  <h3 class="abs" style="left:193px;top:97px;font:500 36px 'Rubik',sans-serif;color:var(--olive)">Injectables</h3>
  <p class="copy abs" style="left:193px;top:155px;width:340px">Injectables (also known as derma fillers) are gel-like substances we use to restore lost volume, smooth out wrinkles, and eliminate or soften facial lines. More than one million men and women per year seek injectable treatments to smooth out their chine, enhance or restore volume to sagging cheeks, or plump up their lips. Injectables also can help improve facial symmetry.</p>
  <a class="btn" href="#" style="left:189px;top:376px;width:135px;height:40px">Read More</a>
  <h3 class="h3 abs" style="left:193px;top:473px">Laser Treatments</h3>
  <h3 class="h3 abs" style="left:193px;top:555px">Micro Needling</h3>
</section>

<section class="other">
  <svg class="abs" style="left:590px;top:0" width="610" height="280"><polygon points="0,0 610,0 610,280" fill="var(--blush)"/></svg>
  <div class="other-photo" role="img" aria-label="Smiling woman with arms raised, in greyscale"></div>
  <p class="abs" style="left:80px;top:160px;font-size:15px;line-height:21px;color:var(--plum)">Chemical<br>peeling</p>
  <svg class="abs" style="left:160px;top:180px" width="200" height="60"><path d="M2 2H128L185 58" stroke="#444" fill="none"/><circle cx="185" cy="58" r="4" fill="var(--plum)"/></svg>
  <h2 class="h2 abs" style="left:662px;top:172px"><span class="accent">Other</span><br>Treatment Options</h2>
  <p class="copy small abs" style="left:665px;top:272px;width:385px">Using a process called chemical peeling, Velora can remove the top layers of skin so healthier looking skin can grow back in its place. A chemical peel is an effective and popular way to treat wrinkles, and scars. Many patients also find a chemical peel the ideal solution to repair sun damage and address other skin issues.</p>
  <a class="btn" href="#" style="left:662px;top:436px;width:134px;height:40px">Read More</a>
</section>

<section class="schedule">
  <svg class="abs" style="left:0;top:0" width="600" height="70"><polygon points="0,0 590,0 0,70" fill="var(--blush)"/></svg>
  <h2 class="h2 abs" style="left:135px;top:85px"><span class="accent">Schedule</span><br>Your Free Consultation</h2>
  <p class="copy abs" style="left:136px;top:185px;width:395px">Why wonder if you’re a candidate for our services when you can so easily find out for yourself? Simply complete and submit this form and a member of our medical team will contact you to schedule your visit. We’ll listen to your concerns, answer your questions, and recommend the best strategy for improving how you look and feel about yourself. That’s the Velora way.</p>
  <div class="field active" style="top:90px">First Name</div>
  <div class="field" style="top:142px">Last Name</div>
  <div class="field" style="top:195px">Email</div>
  <div class="field" style="top:247px">Phone</div>
  <div class="field" style="top:299px">Area of Concern<span class="caret"></span></div>
  <div class="field" style="top:351px">Internet search<span class="caret"></span></div>
  <div class="field" style="top:403px;height:98px;align-items:flex-start;padding-top:12px">Message</div>
  <p class="abs" style="left:620px;top:513px;font-size:11.5px;display:flex;gap:8px;align-items:center"><span style="width:12px;height:12px;border:1px solid #333;display:inline-block"></span><span>I accept the <span style="color:var(--plum)">Terms of Use</span> &amp; agree to receive monthly specials, newsletter, etc*.</span></p>
  <a class="btn" href="#" style="left:620px;top:547px;width:225px;height:41px">Book An Appointment</a>
</section>

<div class="map" role="img" aria-label="Street map showing the Velora Medspa location in Westbrook"></div>

<footer class="site-footer">
  <div class="brand" style="left:60px;top:60px"><span>Velora Medspa</span><span class="dot"></span></div>
  <p class="abs" style="left:62px;top:132px;font-size:12px"><span style="color:var(--plum)">©VELORA MEDSPA</span> - 2023 All rights reserved.</p>
  <h4 class="footer-title abs" style="left:428px;top:50px"><span class="accent">Contact</span> Us</h4>
  <svg class="abs" style="left:426px;top:92px" width="22" height="28" viewBox="0 0 24 30" fill="none" stroke="var(--plum)" stroke-width="1.5"><path d="M12 28s10-10 10-17a10 10 0 00-20 0c0 7 10 17 10 17z"/><circle cx="12" cy="11" r="3.5"/></svg>
  <p class="abs" style="left:465px;top:88px;font-size:13.5px;line-height:24px"><span style="color:var(--plum)">Velora Medspa</span><br>1470 Larkspur<br>Turnpike Westbrook<br>CT 06498</p>
  <svg class="abs" style="left:426px;top:198px" width="24" height="24" viewBox="0 0 24 24" fill="none" stroke="var(--plum)" stroke-width="1.3"><path d="M5 3h4l2 5-2.5 1.5a11 11 0 005 5L15 12l5 2v4a2 2 0 01-2 2A16 16 0 013 5a2 2 0 012-2z"/></svg>
  <p class="abs" style="left:465px;top:200px;font-size:17px">860-555-0142</p>
  <h4 class="footer-title abs" style="left:793px;top:42px"><span class="accent">Site</span>Map</h4>
  <ul class="footer-list abs" style="left:793px;top:84px">
    <li>About</li><li>Injectables</li><li>Laser Treatments</li><li>Micro Needling</li><li>Other Treatment Options</li><li>Contact</li>
  </ul>
</footer>

</body>
</html>
```